Design a Pulsebox Flyer to attract new membership

With constantly updating workouts and the nutritional help Tellmore LiftWorks is more than just an average gym. It’s a place for everyone to get healthy in a stress-free, safe and friendly environment.

Target Market(s)

Women ages 25-60 years old

Industry/Entity Type

Environment

Font styles to use
Serif

Requirements
Must have
• Please read thru the following info before you begin your design:
• Pulsebox Flyer Information
• Please keep in mind a few things:
• 1) Our facility colors orange and green (you can see from my website what the color scheme is)
• 2) Our target demo graphic is women between the ages of 25-60, a large majority of my current clientele are middle aged women 45-60 years old
• 3) Try to keep it clean, and white (like Quintrel's website) if possible
• Side 1: (image of equipment and a younger women working out)
• 1) TLLW Logo
• 2) FREE WEEK TRIAL (big font) Sing up at www.tlliftworks.example/schedulesign-up
• 3) Schedule: Monday-Friday 5:30am – 6:15am – 6:00pm – 7:00pm
• 4) Rates: $150/ Month Unlimited Classes - $100 /10 session package
• *15% discount for all fire, police, military, veterans, teachers, current students & trade association members
• 5) Address: 917 Quill Avenue Staten Island, NY 10304
• 6) Contact info: Phone: 347-555-0182 Email: tlliftworks@mailbox.example
• 7) Website and Social media www.tlliftworks.example find us @TLLiftWorks on Friendloop, Chirpline, Snapgrid, Rateo, Orbix + and spotkeeper
• Side 2 (image of a women working out, preferable middle aged):
• 1) 6 Benefits of PulseBox:
• a. Benefit #1: It BLASTS calories
• b. Benefit #2: It’s great Cardiovascular conditioning
• c. Benefit #3: It increases joint mobility
• d. Benefit #4: Everyday is something different, guaranteed
• e. Benefit #5: You’ll make new friends
• f. Benefit #6: You’ll feel like a badass
• 2) Free Week Trial Class (smaller font at the bottom) sign up at: www.tlliftworks.example/schedulesign-up

```html
<!DOCTYPE html>
<html lang="en">
<head>
<meta charset="utf-8">
<title>Tellmore LiftWorks – Free Week Trial Flyer</title>
<link rel="stylesheet" href="https://fonts.googleapis.com/css2?family=Source+Sans+3:wght@400;600;700;800&display=swap">
<style>
  :root {
    --green: #1c4a35;
    --green-band: #1f4d38;
    --orange: #f4a70b;
    --ink: #3a3a3a;
    --white: #ffffff;
    --page: #ebe8e3;
    --logo-teal: #1d5d55;
  }
  * { margin: 0; padding: 0; box-sizing: border-box; }
  html, body { width: 1200px; height: 960px; overflow: hidden; }
  body {
    background: var(--page);
    font-family: "Source Sans 3", Arial, sans-serif;
    position: relative;
  }
  .flyer {
    position: absolute;
    top: 87px;
    width: 544px;
    height: 771px;
    background: var(--white);
    overflow: hidden;
    box-shadow: 0 3px 10px rgba(0,0,0,.25);
  }
  .flyer--front { left: 48px; }
  .flyer--back { left: 608px; }
  .abs { position: absolute; }
  .center { left: 0; right: 0; text-align: center; white-space: nowrap; }

  .headline-top {
    color: var(--green);
    font-weight: 800;
    font-size: 44px;
    letter-spacing: -1.5px;
    line-height: 1;
    white-space: nowrap;
  }
  .headline-main {
    color: var(--orange);
    font-weight: 800;
    font-size: 84px;
    letter-spacing: -2px;
    line-height: 1;
    white-space: nowrap;
  }
  .signup-label { color: var(--ink); font-size: 22px; line-height: 1; }
  .signup-url { color: var(--ink); font-size: 26px; line-height: 1; letter-spacing: -.3px; }

  .schedule-band {
    top: 218px; height: 27px; left: 0; right: 0;
    background: var(--green);
    color: var(--white);
    font-size: 18px;
    line-height: 27px;
    text-align: center;
    white-space: nowrap;
  }
  .gym-photo {
    top: 245px; left: 0; right: 0; height: 273px;
    background: linear-gradient(160deg, #aeb8c1 0%, #6f7a84 45%, #2f3439 100%);
  }
  .discount-badge { right: 22px; top: 428px; width: 84px; height: 84px; }
  .discount-band {
    top: 518px; height: 28px; left: 0; right: 0;
    background: var(--green);
    color: var(--white);
    font-size: 12px;
    line-height: 28px;
    text-align: center;
    white-space: nowrap;
  }
  .rates { top: 563px; color: var(--ink); font-size: 25px; line-height: 28px; letter-spacing: -.5px; }
  .rates strong { font-weight: 800; }
  .rates .caps { font-size: 22px; }

  .contact-band {
    top: 640px; left: 128px; right: 0; height: 78px;
    background: var(--orange);
    color: var(--white);
    padding: 6px 0 0 10px;
    font-size: 15px;
    line-height: 23px;
    white-space: nowrap;
  }
  .contact-band strong { font-size: 16px; font-weight: 700; }
  .contact-band .gap { display: inline-block; width: 8px; }

  .brand-mark {
    background: var(--logo-teal);
    color: var(--white);
    font-weight: 800;
    text-align: center;
    display: flex;
    align-items: center;
    justify-content: center;
    line-height: 1.05;
    text-transform: uppercase;
    padding: 8px;
  }
  .brand-mark--front { left: 14px; top: 621px; width: 114px; height: 114px; font-size: 17px; }
  .brand-mark--back { left: 15px; top: 464px; width: 112px; height: 112px; font-size: 17px; }

  .social-row {
    display: flex;
    align-items: center;
    gap: 8px;
    font-size: 13px;
    line-height: 1;
    white-space: nowrap;
  }
  .social-row .find b { font-weight: 700; }
  .social-list { display: flex; gap: 6px; }
  .social-item { display: flex; align-items: center; gap: 3px; font-size: 10px; font-weight: 600; white-space: nowrap; }
  .social-item i { width: 9px; height: 9px; border-radius: 50%; background: currentColor; display: inline-block; flex: none; }
  .social-row--front { top: 740px; right: 18px; color: var(--ink); }
  .social-row--front .social-item { color: var(--green); }
  .social-row--back { top: 680px; left: 0; right: 0; justify-content: center; color: var(--white); }

  .benefits-title {
    top: 44px; color: var(--orange);
    font-weight: 800; font-size: 35px; letter-spacing: -.8px; line-height: 1;
  }
  .coach-photo {
    top: 92px; left: 0; width: 300px; height: 346px;
    background: radial-gradient(ellipse at 45% 55%, #d9c2ad 0%, #b9a291 30%, #5a5250 65%, #f4f4f4 100%);
  }
  .benefit {
    color: var(--green);
    font-weight: 700;
    font-size: 14px;
    line-height: 18px;
    text-transform: uppercase;
    display: flex;
    gap: 6px;
    white-space: nowrap;
  }
  .benefit .num { font-size: 23px; font-weight: 800; line-height: 18px; }

  .trial-panel {
    top: 438px; left: 0; right: 0; height: 280px;
    background: var(--green-band);
  }
  .trial-panel .headline-top { color: var(--white); font-size: 42px; }
  .trial-panel .signup-label, .trial-panel .signup-url { color: var(--white); }
  .footer-band {
    top: 718px; left: 0; right: 0; bottom: 0;
    background: var(--orange);
    color: var(--white);
    font-size: 16px;
    text-align: center;
    line-height: 53px;
  }
</style>
</head>
<body>

<section class="flyer flyer--front">
  <div class="abs center headline-top" style="top:42px;">FREE WEEK</div>
  <div class="abs center headline-main" style="top:78px;">TRIAL</div>
  <div class="abs center signup-label" style="top:154px;">Sing up at</div>
  <div class="abs center signup-url" style="top:180px;">www.tlliftworks.example/schedulesign-up</div>

  <div class="abs schedule-band">Monday-Friday 5:30am – 6:15am – 6:00pm – 7:00pm</div>
  <div class="abs gym-photo" role="img" aria-label="Photo of a young woman doing push-ups on dumbbells in a gym with equipment"></div>

  <svg class="abs discount-badge" viewBox="0 0 100 100" aria-label="15% discount">
    <polygon fill="var(--orange)" stroke="#fff" stroke-width="2"
      points="50,2 58,14 72,7 74,22 90,20 85,35 98,42 87,52 96,65 81,69 83,84 68,82 62,96 50,87 38,96 32,82 17,84 19,69 4,65 13,52 2,42 15,35 10,20 26,22 28,7 42,14"/>
    <text x="50" y="56" text-anchor="middle" fill="#fff" font-family="Source Sans 3, sans-serif" font-weight="800" font-size="28">%15</text>
    <text x="50" y="70" text-anchor="middle" fill="#fff" font-family="Source Sans 3, sans-serif" font-weight="600" font-size="9">DISCOUNT</text>
  </svg>

  <div class="abs discount-band">15% discount for all fire, police, military, veterans, teachers, current students &amp; trade association members</div>

  <div class="abs center rates">
    <div><strong>$150</strong>/ <span class="caps">MONTH</span> <strong>UNLIMITED CLASSES</strong></div>
    <div>$100 /10 <strong>SESSION</strong> <span class="caps">PACKAGE</span></div>
  </div>

  <div class="abs contact-band">
    <div>917 Quill Avenue Staten Island, NY 10304</div>
    <div>Phone: <strong>347-555-0182</strong><span class="gap"></span>Email: <strong>tlliftworks@mailbox.example</strong></div>
    <div>www.tlliftworks.example</div>
  </div>
  <div class="abs brand-mark brand-mark--front">Tellmore LiftWorks</div>

  <div class="abs social-row social-row--front">
    <span class="find">Find us @ <b>TLLiftWorks</b> on</span>
    <span class="social-list">
      <span class="social-item"><i></i>Friendloop</span>
      <span class="social-item"><i></i>Chirpline</span>
      <span class="social-item"><i></i>Snapgrid</span>
      <span class="social-item"><i></i>Rateo</span>
      <span class="social-item"><i></i>Orbix +</span>
      <span class="social-item"><i></i>spotkeeper</span>
    </span>
  </div>
</section>

<section class="flyer flyer--back">
  <div class="abs center benefits-title">6 BENEFITS OF PULSEBOX</div>
  <div class="abs coach-photo" role="img" aria-label="Photo of a woman in a black tank top lifting a dumbbell"></div>

  <div class="abs benefit" style="left:280px; top:130px;"><span class="num">1.</span><span>It blasts calories</span></div>
  <div class="abs benefit" style="left:302px; top:170px;"><span class="num">2.</span><span>It’s great cardiovascular<br>conditioning</span></div>
  <div class="abs benefit" style="left:312px; top:231px;"><span class="num">3.</span><span>It increases joint mobility</span></div>
  <div class="abs benefit" style="left:316px; top:271px;"><span class="num">4.</span><span>Everyday is something dif<br>ferent, guaranteed</span></div>
  <div class="abs benefit" style="left:302px; top:333px;"><span class="num">5.</span><span>You’ll make new friends</span></div>
  <div class="abs benefit" style="left:280px; top:383px;"><span class="num">6.</span><span>You’ll feel like a badass</span></div>

  <div class="abs trial-panel">
    <div class="abs headline-top" style="left:168px; top:26px;">FREE WEEK</div>
    <div class="abs headline-main" style="left:158px; top:58px;">TRIAL</div>
    <div class="abs center signup-label" style="top:152px;">Sing up at</div>
    <div class="abs center signup-url" style="top:179px; font-size:22px;">www.tlliftworks.example/schedulesign-up</div>
  </div>
  <div class="abs brand-mark brand-mark--back">Tellmore LiftWorks</div>

  <div class="abs social-row social-row--back">
    <span class="find">Find us @ <b>TLLiftWorks</b> on</span>
    <span class="social-list">
      <span class="social-item"><i></i>Friendloop</span>
      <span class="social-item"><i></i>Chirpline</span>
      <span class="social-item"><i></i>Snapgrid</span>
      <span class="social-item"><i></i>Rateo</span>
      <span class="social-item"><i></i>Orbix +</span>
      <span class="social-item"><i></i>spotkeeper</span>
    </span>
  </div>

  <div class="abs footer-band">www.tlliftworks.example</div>
</section>

</body>
</html>
```